Meadowlark Hollow Candle Company needs a Label design

We need a label design for a new candle company based in Charleston South Carolina. Our mission is to provide people with candles that will fill any space with fragrances that are uplifting, comforting, fresh and will make any space feel like home. Our candles are aromatherapy, 100% soy wax, and hand poured (we would love for this to be indicated somewhere on the label). We would like to see a label that is modern, very clean and uses pastel colors like green, blush pink, mauve and blush blue. The final design should communicate peace, gratitude, hope, and happiness.

```html
<!DOCTYPE html>
<html lang="en">
<head>
<meta charset="UTF-8">
<title>Meadowlark Hollow Candle Company – Fresh Magnolia Petals Label</title>
<link rel="stylesheet" href="https://fonts.googleapis.com/css2?family=Allura&family=Playfair+Display:wght@400&display=swap">
<style>
  :root {
    --page: #ffffff;
    --blush: #f3dfe5;
    --ink: #ffffff;
    --ornament: rgba(255, 255, 255, 0.55);
  }
  * { margin: 0; padding: 0; box-sizing: border-box; }
  html, body {
    width: 927px;
    height: 1200px;
    overflow: hidden;
    background: var(--page);
  }
  .canvas {
    position: relative;
    width: 927px;
    height: 1200px;
  }
  .label {
    position: absolute;
    left: 79px;
    top: 74px;
    width: 762px;
    height: 953px;
    border-radius: 72px;
    background: var(--blush);
    color: var(--ink);
  }
  .brand {
    position: absolute;
    left: 0;
    right: 0;
    top: 118px;
    text-align: center;
    font-family: "Playfair Display", serif;
    font-weight: 400;
    font-size: 34px;
    line-height: 1.15;
    letter-spacing: 1px;
  }
  .scent-name {
    position: absolute;
    left: 0;
    right: 0;
    top: 282px;
    text-align: center;
    font-family: "Allura", cursive;
    font-weight: 400;
    font-size: 104px;
    line-height: 122px;
  }
  .scent-name span { display: block; }
  .flourish {
    position: absolute;
    left: 161px;
    top: 679px;
    width: 440px;
    height: 98px;
    border-radius: 49px;
    background: var(--ornament);
  }
  .features {
    position: absolute;
    left: 0;
    right: 0;
    top: 816px;
    text-align: center;
    font-family: "Playfair Display", serif;
    font-size: 25px;
    font-variant: small-caps;
    font-variant-numeric: oldstyle-nums;
    letter-spacing: 0.2px;
    white-space: nowrap;
  }
</style>
</head>
<body>
  <div class="canvas">
    <section class="label">
      <div class="brand">Meadowlark Hollow<br>Candle Company</div>
      <h1 class="scent-name">
        <span>Fresh</span>
        <span>Magnolia</span>
        <span>Petals</span>
      </h1>
      <div class="flourish" role="img" aria-label="Decorative scroll flourish divider"></div>
      <p class="features">Aromatherapy - Hand Poured - 100% Soy Wax</p>
    </section>
  </div>
</body>
</html>
```